Frostvale Harborline LLC

we need a business card design

Industry/Entity Type

hvac

Contact Information for Business Card

my logo

Requirements
Must have
• my logo and same colors

```html
<!DOCTYPE html>
<html lang="en">
<head>
<meta charset="utf-8">
<title>Frostvale Harborline LLC – Business Card</title>
<link href="https://fonts.googleapis.com/css2?family=Montserrat:wght@400;500;700&display=swap" rel="stylesheet">
<style>
  :root {
    --navy: #0b3a99;
    --navy-deep: #062f86;
    --cyan: #12a9e0;
    --ink: #1b1f2a;
    --rule: #1d2b57;
    --paper: #ffffff;
    --backdrop: #e9ecf1;
  }
  html, body {
    margin: 0;
    width: 1200px;
    height: 1200px;
    overflow: hidden;
    background: var(--backdrop);
    font-family: "Montserrat", Arial, sans-serif;
  }
  .sheet {
    position: relative;
    width: 1200px;
    height: 1200px;
  }
  .card {
    position: absolute;
    left: 150px;
    width: 900px;
    height: 514px;
    border-radius: 36px;
    overflow: hidden;
    box-shadow: 0 8px 24px rgba(10, 30, 70, 0.18);
  }
  .card--front { top: 48px; background: var(--paper); }
  .card--back {
    top: 620px;
    background: radial-gradient(ellipse at 50% 45%, #0d46b0 0%, var(--navy) 55%, var(--navy-deep) 100%);
    display: flex;
    align-items: center;
    justify-content: center;
  }
  .card__band { position: absolute; inset: 0; }
  .brand {
    position: absolute;
    display: flex;
    align-items: center;
    gap: 16px;
    font-weight: 700;
    line-height: 1.15;
  }
  .brand__mark { width: 22px; height: 22px; flex: none; }
  .brand--front {
    top: 110px;
    left: 430px;
    color: var(--navy);
    font-size: 34px;
  }
  .brand--front .brand__mark { background: var(--navy); }
  .brand--back {
    position: static;
    color: #ffffff;
    font-size: 50px;
  }
  .brand--back .brand__mark { background: #ffffff; width: 30px; height: 30px; }
  .person {
    position: absolute;
    left: 60px;
    top: 252px;
  }
  .person__name {
    margin: 0;
    color: var(--cyan);
    font-size: 40px;
    font-weight: 700;
    letter-spacing: 0.5px;
    line-height: 1.2;
  }
  .person__title {
    margin: 2px 0 0;
    color: var(--ink);
    font-size: 26px;
    font-weight: 400;
  }
  .person__rule {
    width: 460px;
    height: 2px;
    background: var(--rule);
    margin: 10px 0 8px;
  }
  .contact {
    display: flex;
    align-items: center;
    gap: 14px;
    color: var(--ink);
    font-size: 26px;
    margin: 4px 0;
  }
  .contact svg { width: 26px; height: 26px; flex: none; }
  .email-rule {
    position: absolute;
    right: 60px;
    top: 290px;
    width: 440px;
    height: 2px;
    background: var(--rule);
  }
  .email {
    position: absolute;
    right: 60px;
    top: 312px;
    display: flex;
    align-items: center;
    gap: 12px;
    color: var(--ink);
    font-size: 25px;
  }
  .email svg { width: 30px; height: 22px; }
  .website {
    position: absolute;
    right: 60px;
    top: 428px;
    color: #ffffff;
    font-size: 25px;
    letter-spacing: 1px;
  }
</style>
</head>
<body>
<main class="sheet">
  <section class="card card--front" aria-label="Business card front">
    <svg class="card__band" viewBox="0 0 900 514" preserveAspectRatio="none" aria-hidden="true">
      <path d="M0,482 C250,482 390,476 450,438 C490,408 510,362 570,362 L900,362"
            fill="none" stroke="var(--cyan)" stroke-width="6"/>
      <path d="M0,494 C250,494 400,488 460,450 C500,420 520,376 580,376 L900,376 L900,514 L0,514 Z"
            fill="var(--navy)"/>
    </svg>

    <div class="brand brand--front">
      <span class="brand__mark"></span>
      <span>Frostvale Harborline<br>LLC</span>
    </div>

    <div class="person">
      <h1 class="person__name">FULL NAME</h1>
      <p class="person__title">TITLE</p>
      <div class="person__rule"></div>
      <div class="contact">
        <svg viewBox="0 0 24 24" aria-hidden="true"><path fill="var(--cyan)" d="M6.6 10.8a15.1 15.1 0 0 0 6.6 6.6l2.2-2.2c.3-.3.7-.4 1-.2 1.1.4 2.3.6 3.6.6.6 0 1 .4 1 1V20c0 .6-.4 1-1 1C10.6 21 3 13.4 3 4c0-.6.4-1 1-1h3.5c.6 0 1 .4 1 1 0 1.3.2 2.5.6 3.6.1.3 0 .7-.2 1z"/></svg>
        <span>(000) 000 0000</span>
      </div>
      <div class="contact">
        <svg viewBox="0 0 24 24" aria-hidden="true"><rect x="6" y="2" width="12" height="20" rx="2" fill="none" stroke="var(--cyan)" stroke-width="2"/><circle cx="12" cy="18.5" r="1" fill="var(--cyan)"/></svg>
        <span>(000) 000 0000</span>
      </div>
    </div>

    <div class="email-rule"></div>
    <div class="email">
      <svg viewBox="0 0 30 22" aria-hidden="true"><rect width="30" height="22" fill="var(--cyan)"/><path d="M0,0 L15,12 L30,0" fill="none" stroke="#ffffff" stroke-width="2"/></svg>
      <span>hello@frostvale.example</span>
    </div>
    <div class="website">www.frostvale.example</div>
  </section>

  <section class="card card--back" aria-label="Business card back">
    <div class="brand brand--back">
      <span class="brand__mark"></span>
      <span>Frostvale Harborline<br>LLC</span>
    </div>
  </section>
</main>
</body>
</html>
```